Business Card Design - Amberfield Court

We are looking at a new design for our business cards that has a modern and professional look. We run a residential aged care facility focussing on the care of residents. The cards will be used for potential clients, consultants and business opportunities in this sector. Blue and white is our main colours and would to see these colours incorporated in the design.
Industry/Entity Type
Business
Contact Information for Business Card
Amberfield Court, Darren Walsh, dwalsh@amberfieldcourt.com.au, Finance Manager, 0472 639 208, BCom, 37 Marrabel Crescent, Brindle Vale, Qld 4093.
Look and feel
Each slider illustrates characteristics of the customer's brand and the style your logo design should communicate.

```html
<!DOCTYPE html>
<html lang="en">
<head>
<meta charset="utf-8">
<title>Amberfield Court – Business Card</title>
<link rel="stylesheet" href="https://fonts.googleapis.com/css2?family=Open+Sans:ital,wght@0,400;0,600;1,400&display=swap">
<style>
  :root {
    --backdrop: #8e8e8e;
    --paper: #f3f3f4;
    --brand-blue: #43697f;
    --name-blue: #3f6787;
    --muted-grey: #8b8681;
    --ink: #3a3a3a;
    --rule: #8f8f8f;
    --on-blue: #f4f4f4;
  }
  * { box-sizing: border-box; margin: 0; padding: 0; }
  html, body {
    width: 1105px; height: 1200px; overflow: hidden;
    background: var(--backdrop);
    font-family: "Open Sans", Arial, sans-serif;
  }
  .card {
    position: absolute; left: 102px;
    width: 900px; height: 513px;
  }
  .card--front { top: 57px; background: var(--paper); }
  .card--back { top: 630px; background: var(--brand-blue); }

  .brand-name {
    position: absolute; right: 48px; top: 190px;
    font-size: 34px; font-weight: 600; color: var(--brand-blue);
    letter-spacing: 0.5px; white-space: nowrap;
  }
  .person {
    position: absolute; left: 42px; top: 283px;
    font-size: 30px; font-weight: 600; color: var(--name-blue);
  }
  .person .credential { font-size: 22px; }
  .role-line {
    position: absolute; left: 42px; top: 326px; right: 47px;
    display: flex; align-items: center;
  }
  .role {
    font-size: 22px; color: var(--muted-grey); white-space: nowrap;
  }
  .role-line .rule {
    flex: 1; height: 1px; background: var(--rule); margin-left: 2px; margin-top: 4px;
  }
  .contacts {
    position: absolute; left: 44px; top: 378px; list-style: none;
  }
  .contacts li {
    display: flex; align-items: center; height: 33.5px;
    font-size: 22px; color: var(--ink);
  }
  .contacts svg { width: 20px; height: 20px; margin-right: 16px; fill: var(--brand-blue); }
  .address {
    position: absolute; right: 47px; top: 412px;
    text-align: right; font-size: 22px; line-height: 33.5px; color: var(--ink);
  }

  .back-name {
    position: absolute; left: 0; right: 0; top: 232px;
    text-align: center; font-size: 44px; font-weight: 600; color: var(--on-blue);
    letter-spacing: 1px;
  }
  .back-web {
    position: absolute; left: 0; right: 0; top: 338px;
    text-align: center; font-size: 25px; font-style: italic; color: var(--on-blue);
    letter-spacing: 2px;
  }
</style>
</head>
<body>
  <section class="card card--front">
    <div class="brand-name">Amberfield Court</div>

    <div class="person">Darren Walsh <span class="credential">BCom</span></div>
    <div class="role-line"><span class="role">Finance Manager</span><span class="rule"></span></div>

    <ul class="contacts">
      <li>
        <svg viewBox="0 0 20 20" aria-hidden="true"><path d="M4.5 1.5l3 3.2-1.8 2.3c1.2 2.6 3.6 5 6.3 6.3l2.3-1.8 3.2 3-2 2.7C8.6 18.2 1.8 11.4 1.8 4.3z"/></svg>
        0472 639 208
      </li>
      <li>
        <svg viewBox="0 0 20 20" aria-hidden="true"><path d="M2 4h16v12H2z M3.5 5.5L10 10.5l6.5-5" fill="none" stroke="var(--brand-blue)" stroke-width="0"/><path d="M2 4h16v2l-8 5-8-5z"/><path d="M2 8l8 5 8-5v8H2z"/></svg>
        dwalsh@amberfieldcourt.com.au
      </li>
      <li>
        <svg viewBox="0 0 20 20" aria-hidden="true"><circle cx="10" cy="10" r="8.5"/><path d="M6 5c2 0 3 1.5 2.5 3S6 9 6.5 11s2 2 1.5 4M12 4c-.5 2 1 2.5 2.5 2.5M13 11c1 .5 1.5 2 1 4" fill="none" stroke="var(--paper)" stroke-width="1.6"/></svg>
        www.amberfieldcourt.com.au
      </li>
    </ul>

    <div class="address">37 Marrabel Crescent<br>Brindle Vale, Qld 4093.</div>
  </section>

  <section class="card card--back">
    <div class="back-name">Amberfield Court</div>
    <div class="back-web">www.amberfieldcourt.com.au</div>
  </section>
</body>
</html>
```